Dental Website offering Continuing Educational Courses

Need a Wordpress CMS design for a dentist website which will offer continuing education courses. The design should be professional, simple and elegant. Logo versions are provided. Please follow those colors plus one or two others that will blend well. Here's examples of other sites they like - www.pulpvantage.com, www.kqtorvi.com, www.thebrightwellinstitute.com., www.plqma.org/. Please provide designs in jpg format. If selected, then final design will be required in psd format.

Target Market(s)

dentists, endodontists (root canal specialists)

Industry/Entity Type

Education

Requirements
Must have
• Combination Horizontal / Vertical navigation. Place course titles in vertical nav in a side bar on home page. List them as Course 1, Course 2 ,etc.. total of 7 courses. The header horizontal nav should be; Home, About, Courses, Doctor Name, Faculty, FAQ, Patients, Contact.
Need placeholder to accommodate one large static image just under main nav. Need web safe fonts. Need placeholder for calendar like this example www.quietharbors.org/. Need to show a dropdown menu example. Design for 1024 x 768. Need space on home page to allow for logos of external websites/ associations. These are; www.truefieldpulp.com, www.mavolix.com, www.wfk.org/, www.kintovarhq.com/kinto/. Would like to see a row of images across the bottom of the home page like the www.plqma.org site has. Would like to show a Contact Form on the home page like the "need assistance" form example on www.thebrightwellinstitute.com. Would like to create a placeholder on the home page for an image of a doctor.
Nice to have
• 3 or 4 column footer (which features sitemap, copyright, etc..). Examples in the design for the web site’s copy styling:
o through headers
o Bulleted list
o Hyperlink
o Table

```html
<!DOCTYPE html>
<html lang="en">
<head>
<meta charset="utf-8">
<title>VARO Learning — Continuing Education</title>
<link href="https://fonts.googleapis.com/css2?family=Cinzel:wght@600&display=swap" rel="stylesheet">
<style>
:root{
  --page-dark:#0a4a9a;
  --page-mid:#0d5db5;
  --page-light:#1f7fdc;
  --top-band:#06346e;
  --panel:#ffffff;
  --nav-text:#ffffff;
  --link-blue:#1565c0;
  --grey-text:#8a8a8a;
  --body-text:#6e6e6e;
  --green:#8bab1d;
  --green-dark:#6f8c12;
  --orange:#e8651a;
  --red:#d2213a;
  --field-line:#b9b9b9;
  --footer-text:#a0a0a0;
}
*{box-sizing:border-box;margin:0;padding:0}
html,body{width:1100px;height:1200px;overflow:hidden}
body{
  position:relative;
  font-family:Arial, Helvetica, sans-serif;
  background:linear-gradient(100deg,var(--page-dark) 0%,var(--page-mid) 55%,var(--page-light) 100%);
}
.top-band{position:absolute;left:0;top:0;width:1100px;height:16px;background:var(--top-band)}
.abs{position:absolute}
.panel{position:absolute;background:var(--panel)}

.brand{left:0;top:44px;width:1100px;display:flex;justify-content:center;align-items:center;gap:14px}
.brand-mark{width:30px;height:30px;background:#fff}
.brand-name{color:#fff;font-weight:700;font-size:44px;line-height:1;letter-spacing:1px}

.main-nav a{position:absolute;top:143px;color:var(--nav-text);font-weight:700;font-size:15px;text-decoration:none;transform:translateX(-50%);white-space:nowrap;letter-spacing:.5px}
.dropdown{left:282px;top:169px;width:136px;height:107px;background:#fff;padding:8px 0 0 38px;z-index:2}
.dropdown a{display:block;color:var(--link-blue);font-weight:700;font-size:13px;line-height:24px;text-decoration:none}
.dropdown a.active{color:#123a6a;text-decoration:underline}

.hero{left:102px;top:192px;width:898px;height:239px}
.hero-image{position:absolute;left:6px;top:6px;width:656px;height:225px;background:linear-gradient(90deg,#c98f6e 0%,#e7c2a8 30%,#b07a5a 55%,#d9b49a 80%,#8a6a58 100%)}
.calendar{position:absolute;left:679px;top:23px;width:205px;height:195px;background:#eeeeee;border:1px solid #d8d8d8;border-radius:6px;padding:6px 10px}
.cal-head{display:flex;justify-content:space-between;font-family:Georgia, serif;font-size:12px;font-weight:700;color:#555;padding:6px 6px 4px}
.calendar table{width:100%;border-collapse:separate;border-spacing:3px}
.calendar th{font-size:11px;color:#666;font-weight:700;height:17px}
.calendar td{font-size:11px;color:#444;text-align:center;background:#fff;border:1px solid #d0d0d0;height:17px}
.calendar td.muted{color:#c8c8c8}
.calendar td.today{font-weight:700}
.calendar td.selected{background:#8a8a8a;color:#fff;border-color:#777}

.sidebar{left:102px;top:446px;width:226px;height:366px}
.ribbon{left:90px;top:454px;z-index:2}
.ribbon span{position:absolute;left:24px;top:6px;font-family:Cinzel, serif;font-size:24px;color:#fff}
.course-list{list-style:none;position:absolute;left:24px;top:62px}
.course-list li{font-size:13px;font-weight:700;color:var(--grey-text);height:30px;padding-left:22px;position:relative}
.course-list li::before{content:"";position:absolute;left:3px;top:4px;border-left:5px solid #777;border-top:3px solid transparent;border-bottom:3px solid transparent}

.signup{left:102px;top:828px;width:226px;height:77px}
.signup .field{position:absolute;left:10px;top:24px;width:164px;height:31px;border:1px solid #ddd;font-size:12px;color:#999;padding:8px 9px}
.signup .go{position:absolute;left:174px;top:22px;width:42px;height:34px;background:#5e5e5e;color:#fff;font-weight:700;font-size:20px;text-align:center;line-height:34px}

.welcome{left:344px;top:446px;width:656px;height:194px}
.welcome h1{position:absolute;left:10px;top:14px;font-weight:400;font-size:25px;color:var(--green)}
.welcome p{position:absolute;left:10px;top:54px;width:400px;font-size:12.5px;line-height:20px;color:var(--body-text)}
.welcome .more{position:absolute;left:284px;top:148px;font-size:11px;font-weight:700;color:var(--grey-text);text-decoration:none}
.doctor-image{position:absolute;right:0;top:0;width:229px;height:194px;background:linear-gradient(90deg,#ffffff 0%,#e6eef2 40%,#c9d9e2 100%)}

.videos{left:344px;top:658px;width:383px;height:247px}
.tab{position:absolute;left:4px;top:4px}
.tab span{position:absolute;left:12px;top:10px;font-size:15px;font-weight:700;color:#fff}
.video-frame{position:absolute;left:66px;top:50px;width:253px;height:186px;background:#111;padding:8px}
.video-still{width:237px;height:152px;background:linear-gradient(135deg,#d8a584,#f0d2bd 50%,#a5765b)}
.video-bar{height:12px;margin-top:4px;background:#ddd;position:relative}
.video-bar::before{content:"";position:absolute;left:20px;top:5px;width:150px;height:2px;background:#888}

.assist{left:746px;top:658px;width:254px;height:247px}
.form-field{position:absolute;left:16px;width:208px;height:25px;border:1px solid var(--field-line);font-size:10px;color:#888;padding:6px 7px;letter-spacing:.3px}
.form-field.area{height:46px}
.submit{position:absolute;left:170px;top:220px;width:56px;height:20px;background:#111;color:#fff;font-size:10px;text-align:center;line-height:20px;border-radius:3px}

.gallery{left:102px;top:927px;width:898px;height:123px}
.thumb{position:absolute;top:9px;width:166px;height:104px;border:1px solid #bbb}

.site-footer{left:102px;top:1063px;width:898px;height:105px}
.foot-col{position:absolute;top:12px;list-style:none}
.foot-col li{font-size:12px;color:var(--footer-text);line-height:22px}
.foot-note{position:absolute;left:733px;top:12px;width:130px;font-size:12px;color:var(--footer-text);line-height:22px}
.social{position:absolute;left:736px;top:81px;display:flex;gap:6px}
.social span{width:16px;height:16px;border-radius:3px}
.copyright{left:0;top:1182px;width:1100px;text-align:center;font-size:11px;color:#cfe2f7}
</style>
</head>
<body>
<div class="top-band"></div>

<header class="abs brand">
  <span class="brand-mark"></span>
  <span class="brand-name">VARO Learning</span>
</header>

<nav class="main-nav">
  <a href="#" style="left:149px">HOME</a>
  <a href="#" style="left:236px">ABOUT</a>
  <a href="#" style="left:348px">COURSES</a>
  <a href="#" style="left:489px">DOCTOR NAME</a>
  <a href="#" style="left:625px">FACULTY</a>
  <a href="#" style="left:723px">FAQ</a>
  <a href="#" style="left:823px">PATIENTS</a>
  <a href="#" style="left:943px">CONTACT</a>
</nav>
<div class="abs dropdown">
  <a href="#">Course 1</a>
  <a href="#" class="active">Course 2</a>
  <a href="#">Course 3</a>
  <a href="#">Course 4</a>
</div>

<section class="panel hero">
  <div class="hero-image" role="img" aria-label="Large banner photo of smiling students"></div>
  <div class="calendar">
    <div class="cal-head"><span>&laquo;</span><span>January 2012</span><span>&raquo;</span></div>
    <table>
      <tr><th>Su</th><th>Mo</th><th>Tu</th><th>We</th><th>Th</th><th>Fr</th><th>Sa</th></tr>
      <tr><td class="muted">25</td><td class="muted">26</td><td class="muted">27</td><td class="muted">28</td><td class="muted">29</td><td class="muted">30</td><td>1</td></tr>
      <tr><td>2</td><td>3</td><td>4</td><td>5</td><td>6</td><td>7</td><td>8</td></tr>
      <tr><td>9</td><td>10</td><td>11</td><td>12</td><td>13</td><td class="today">14</td><td>15</td></tr>
      <tr><td>16</td><td>17</td><td>18</td><td>19</td><td>20</td><td class="selected">21</td><td>22</td></tr>
      <tr><td>23</td><td>24</td><td>25</td><td>26</td><td>27</td><td>28</td><td>29</td></tr>
      <tr><td>30</td><td class="muted">1</td><td class="muted">2</td><td class="muted">3</td><td class="muted">4</td><td class="muted">5</td><td class="muted">6</td></tr>
    </table>
  </div>
</section>

<aside class="panel sidebar">
  <ul class="course-list">
    <li>Course 1</li><li>Course 2</li><li>Course 3</li><li>Course 4</li><li>Course 5</li>
    <li>Course 6</li><li>Course 7</li><li>Course 8</li><li>Course 9</li>
  </ul>
</aside>
<div class="abs ribbon">
  <svg width="218" height="43" viewBox="0 0 218 43"><polygon points="0,0 218,0 204,21.5 218,43 0,43" fill="var(--green)"/><polygon points="0,43 12,43 12,50" fill="var(--green-dark)"/></svg>
  <span>COURSE</span>
</div>

<div class="panel signup">
  <div class="field">Enter your email</div>
  <div class="go">GO</div>
</div>

<section class="panel welcome">
  <h1>WELCOME TO VARO</h1>
  <p>Lorem ipsum dolor sit amet,consectetuadipiscing elit.Cimperdiet Lorem ipsum dolovfsdrras imperdiet Lorem ipsum dolor sit amet,consectetua-dipiscing elit.Cras imperdiet Lorem ipsum dolor sit amet,consectetua-Lorem i sum dolor sit amet,consectetuadipiscing elit.Cras imperdiet Lorem ipsum</p>
  <a class="more" href="#">Read more &gt;&gt;</a>
  <div class="doctor-image" role="img" aria-label="Photo of a smiling doctor with a young patient"></div>
</section>

<section class="panel videos">
  <div class="tab">
    <svg width="206" height="38" viewBox="0 0 206 38"><polygon points="0,0 186,0 206,19 186,38 0,38" fill="var(--orange)"/><polyline points="178,11 186,19 178,27" fill="none" stroke="#fff" stroke-width="3"/></svg>
    <span>VIDEOS</span>
  </div>
  <div class="video-frame">
    <div class="video-still" role="img" aria-label="Video preview of a smiling patient"></div>
    <div class="video-bar"></div>
  </div>
</section>

<section class="panel assist">
  <div class="tab">
    <svg width="196" height="38" viewBox="0 0 196 38"><polygon points="0,0 176,0 196,19 176,38 0,38" fill="var(--red)"/><polyline points="168,11 176,19 168,27" fill="none" stroke="#fff" stroke-width="3"/></svg>
    <span>NEED ASSISTANCE?</span>
  </div>
  <div class="form-field" style="top:49px">NAME</div>
  <div class="form-field" style="top:79px">EMAIL</div>
  <div class="form-field" style="top:109px">PHONE NO</div>
  <div class="form-field" style="top:139px">CHOOSE A TOPIC</div>
  <div class="form-field area" style="top:170px">COMMENTS</div>
  <div class="submit">SUBMIT</div>
</section>

<section class="panel gallery">
  <div class="thumb" style="left:26px;background:linear-gradient(#6f97c4,#b7c8a6 60%,#4d6b2f)" role="img" aria-label="Photo of a white colonial mansion"></div>
  <div class="thumb" style="left:196px;background:linear-gradient(#b9c6e4,#eef1f8 60%,#c9d0e0)" role="img" aria-label="Photo of cannons in a snowy field"></div>
  <div class="thumb" style="left:367px;background:linear-gradient(#8fb0d4,#b89a74 55%,#6d7d3f)" role="img" aria-label="Photo of a historic brick house"></div>
  <div class="thumb" style="left:537px;background:linear-gradient(#7aa0cc,#9a6a52 55%,#5e6e48)" role="img" aria-label="Photo of a campus building with a fountain"></div>
  <div class="thumb" style="left:708px;background:linear-gradient(#a9c4e0,#7f8f5c 55%,#4e6532)" role="img" aria-label="Photo of a wooden pergola in a garden"></div>
</section>

<footer class="panel site-footer">
  <ul class="foot-col" style="left:18px"><li>Home</li><li>About</li><li>Courses</li><li>Doctor Name</li></ul>
  <ul class="foot-col" style="left:163px"><li>Faculty</li><li>FAQ</li><li>Patients</li><li>Contact</li></ul>
  <ul class="foot-col" style="left:290px"><li>Why Choose Us</li><li>Testimonials</li><li>Press Clips</li><li>Photo Gallery</li></ul>
  <ul class="foot-col" style="left:434px"><li>Enquiry</li><li>Registration</li><li>Feedback</li></ul>
  <p class="foot-note">Lorem ipsum dolor sit amet, consectetuer adipiscing elit.</p>
  <div class="social">
    <span style="background:#3b5998"></span><span style="background:#33aadd"></span><span style="background:#0e76a8"></span><span style="background:#cc2200"></span>
  </div>
</footer>

<p class="abs copyright">&copy; 2012. All rights reserved</p>
</body>
</html>
```